Erotic romance novelist requires book cover design for new trilogy

I have written a trilogy of erotic romance novels about a young woman and two young men at a northern university, who begin a house share as strangers. The girl is attracted to both men and vice versa. The house is sometimes claustrophobic as the men vie for her attentions and she ultimately chooses neither, thus a delicate menage à trois develops. In the later books of the trilogy, a slowly developing intimate relationship between the two men is explored further and the love and friendship between the three of them is cemented. The chosen design will set the atmosphere for the remaining two book covers in the trilogy. I would like it to be delicately oblique and suggestive.

Target Market(s)

young adults and women aged 18-50

Font styles to use
Decorative
Script

Colors

Designer to choose colors to be used in the design.

Requirements
Must have
• The trilogy is called Pelham Lane and book 1 is called Falling Inward
• I would like a subtle reference to the 'trhreesome' nature of the story
Nice to have
• The female student is studying art history and has an interest in greek sculpture - I have added an inspirational photo

```html
<!DOCTYPE html>
<html lang="en">
<head>
<meta charset="UTF-8">
<title>Pelham Lane – Book 1 – Falling Inward</title>
<link href="https://fonts.googleapis.com/css2?family=Cinzel:wght@400&family=Pinyon+Script&family=Montserrat:wght@400&display=swap" rel="stylesheet">
<style>
  :root {
    --backdrop: #c9d1d3;
    --cover-black: #050505;
    --figure-light: #8a8a8a;
    --figure-mid: #3a3a3a;
    --type-white: #f4f4f2;
    --accent-red: #e0161f;
  }
  html, body {
    margin: 0;
    padding: 0;
    width: 1200px;
    height: 800px;
    overflow: hidden;
    background: var(--backdrop);
  }
  .canvas {
    position: relative;
    width: 1200px;
    height: 800px;
    display: flex;
    align-items: center;
    justify-content: center;
  }
  .cover {
    position: relative;
    width: 500px;
    height: 760px;
    background: var(--cover-black);
    overflow: hidden;
  }
  .cover-figure {
    position: absolute;
    left: 90px;
    top: 150px;
    width: 320px;
    height: 600px;
    background:
      radial-gradient(ellipse 45% 30% at 50% 62%, var(--figure-light) 0%, var(--figure-mid) 55%, transparent 100%),
      radial-gradient(ellipse 35% 22% at 45% 25%, var(--figure-mid) 0%, transparent 100%);
    opacity: 0.9;
  }
  .series-name {
    position: absolute;
    top: 34px;
    left: 0;
    right: 0;
    text-align: center;
    font-family: "Cinzel", serif;
    font-size: 31px;
    letter-spacing: 3px;
    color: var(--type-white);
  }
  .book-number {
    position: absolute;
    top: 90px;
    left: 0;
    right: 0;
    text-align: center;
    font-family: "Montserrat", sans-serif;
    font-size: 22px;
    letter-spacing: 3px;
    color: var(--accent-red);
  }
  .book-title {
    position: absolute;
    top: 140px;
    left: 0;
    right: 0;
    margin: 0;
    font-family: "Pinyon Script", cursive;
    font-weight: 400;
    color: var(--type-white);
    line-height: 1;
  }
  .book-title .line-one {
    display: block;
    font-size: 96px;
    padding-left: 70px;
  }
  .book-title .line-two {
    display: block;
    font-size: 96px;
    padding-left: 150px;
    margin-top: 40px;
  }
  .theme-word {
    position: absolute;
    top: 515px;
    left: 0;
    right: 0;
    text-align: center;
    font-family: "Cinzel", serif;
    font-size: 34px;
    letter-spacing: 3px;
    color: var(--type-white);
  }
</style>
</head>
<body>
  <main class="canvas">
    <article class="cover">
      <div class="cover-figure" role="img" aria-label="Black and white photograph of a crouching figure hugging its knees, lit softly from above"></div>
      <p class="series-name">Pelham Lane</p>
      <p class="book-number">BOOK 1</p>
      <h1 class="book-title">
        <span class="line-one">Falling</span>
        <span class="line-two">Inward</span>
      </h1>
      <p class="theme-word">THREESOME</p>
    </article>
  </main>
</body>
</html>
```